Broschüre für Personaldienstleister
Zielgruppe
Wir sind ein Personaldienstleister und vermitteln ausländisches medizinisches Fachpersonal an deutsche Einrichtungen. Unsere Zielgruppe sind Krankenhäuser, Pflegeheime, Ärztehäuser, Praxen, Labore und weitere medizinische Institutionen.
Aufgabenstellung
Wir haben eine Infobroschüre sowie eine PowerPoint Präsentation bereits mit einem groben Design erstellt. Texte und Beispielbilder (Stockmaterial) sind ebenfalls vorhanden, gerne wünschen wir uns auch Eigeninitiative bei der Wahl der Bilder passend zum neuen Design.
Wir wünschen uns ein Redesign mit einem kreativen, einzigartigen Design. Zudem ist uns wichtig, dass unsere Infografiken qualitativ und hochwertig gestaltet werden.
Dieses Projekt ist mit zukünftigen Folgeprojekten verbunden, da wir weitere Präsentationen und Broschüren für andere Zielgruppen benötigen.

```html
<!DOCTYPE html>
<html lang="de">
<head>
<meta charset="utf-8">
<title>In 6 Schritten zu Ihrer neuen Fachkraft – Broschüre</title>
<link href="https://fonts.googleapis.com/css2?family=Rubik:wght@500;700&family=Montserrat:wght@400;600&display=swap" rel="stylesheet">
<style>
  :root{
    --teal-dark:#133b3d;
    --teal-deep:#1e4a4b;
    --teal-mid:#2f5758;
    --green:#3f7f6c;
    --green-light:#a9c8bb;
    --line-gray:#b9b9b9;
    --page-light:#f1f1f1;
    --page-mid:#d6d6d6;
    --disc:#f4f4f4;
    --text-dark:#1d3d3e;
    --text-body:#3c4748;
    --title-accent:#5d7f7a;
    --white:#ffffff;
    --backdrop:#e6e6e6;
  }
  *{box-sizing:border-box;margin:0;padding:0}
  html,body{width:1200px;height:826px;overflow:hidden;background:var(--backdrop)}
  .spread{position:absolute;left:20px;top:20px;width:1160px;height:786px;display:flex;box-shadow:0 6px 24px rgba(0,0,0,.18)}
  .page{position:relative;width:580px;height:786px;overflow:hidden}

  /* left page */
  .page--steps{background:linear-gradient(100deg,var(--page-mid) 0%,var(--page-light) 55%,#e4e4e4 100%)}
  .steps-title{position:absolute;left:40px;top:54px;font:700 27px/1.1 "Rubik",sans-serif;color:var(--text-dark);letter-spacing:.2px;white-space:nowrap}
  .steps-title__accent{color:var(--title-accent)}
  .timeline{position:absolute;left:0;top:0}
  .step-text{position:absolute;font:400 8.6px/1.28 "Montserrat",sans-serif;color:var(--text-body)}
  .step-text h3{font:600 9px/1.3 "Montserrat",sans-serif;color:var(--text-dark)}
  .step-text--left{left:24px;width:215px}
  .step-text--right{left:405px;width:165px;text-align:justify;hyphens:auto}
  .contact-band{position:absolute;left:0;bottom:0;width:100%;height:46px;background:var(--teal-dark);display:flex;align-items:center;justify-content:space-around;font:400 10px "Montserrat",sans-serif;color:var(--white);letter-spacing:.4px}

  /* right page */
  .page--firstday{background:linear-gradient(160deg,#2c5859 0%,var(--teal-dark) 35%,#0f3133 100%)}
  .firstday-heading{position:absolute;left:28px;top:44px;font:700 21px/1 "Rubik",sans-serif;color:var(--white)}
  .firstday-copy{position:absolute;left:28px;top:72px;width:520px;font:400 8.6px/1.35 "Montserrat",sans-serif;color:var(--white)}
  .firstday-photo{position:absolute;left:150px;top:150px;width:430px;height:636px;
    background:radial-gradient(ellipse at 55% 18%,rgba(176,120,90,.85) 0%,rgba(120,70,45,.7) 18%,rgba(0,0,0,0) 34%),
               radial-gradient(ellipse at 52% 68%,#3f86d4 0%,#3b7cc7 35%,rgba(59,124,199,0) 62%);}
</style>
</head>
<body>
<main class="spread">

  <section class="page page--steps">
    <h1 class="steps-title">In 6 Schritten zu Ihrer neuen <span class="steps-title__accent">Fachkraft</span></h1>

    <svg class="timeline" width="580" height="786" viewBox="0 0 580 786" aria-hidden="true">
      <line x1="290" y1="140" x2="290" y2="678" stroke="var(--line-gray)" stroke-width="8"/>

      <!-- step 1 -->
      <g transform="translate(0,-35)">
        <line x1="190" y1="175" x2="450" y2="175" stroke="var(--green)" stroke-width="7"/>
        <circle cx="190" cy="175" r="13" fill="var(--teal-deep)"/>
        <circle cx="290" cy="175" r="38" fill="var(--disc)" stroke="var(--teal-deep)" stroke-width="8"/>
        <circle cx="450" cy="175" r="20" fill="var(--disc)" stroke="var(--teal-deep)" stroke-width="6"/>
        <text x="450" y="181" text-anchor="middle" font-family="Rubik,sans-serif" font-weight="700" font-size="16" fill="var(--teal-deep)">1</text>
        <g fill="none" stroke="var(--teal-deep)" stroke-width="2">
          <rect x="273" y="162" width="28" height="24" rx="2"/><circle cx="287" cy="171" r="4"/><path d="M280 182q7-7 14 0"/><path d="M304 164v20"/>
        </g>
      </g>

      <!-- step 2 -->
      <g transform="translate(0,-35)">
        <line x1="110" y1="275" x2="365" y2="275" stroke="var(--teal-deep)" stroke-width="7"/>
        <circle cx="365" cy="275" r="13" fill="var(--green)"/>
        <circle cx="290" cy="275" r="38" fill="var(--disc)" stroke="var(--green)" stroke-width="8"/>
        <circle cx="110" cy="275" r="20" fill="var(--disc)" stroke="var(--green)" stroke-width="6"/>
        <text x="110" y="281" text-anchor="middle" font-family="Rubik,sans-serif" font-weight="700" font-size="16" fill="var(--teal-deep)">2</text>
        <path d="M276 260h18l8 8v20h-26z" fill="var(--teal-deep)"/>
        <g stroke="var(--disc)" stroke-width="2.2"><path d="M280 270h10M280 276h14M280 282h10"/></g>
      </g>

      <!-- step 3 -->
      <g transform="translate(0,-35)">
        <line x1="210" y1="375" x2="450" y2="375" stroke="var(--teal-mid)" stroke-width="7"/>
        <circle cx="210" cy="375" r="13" fill="var(--green-light)"/>
        <circle cx="290" cy="375" r="38" fill="var(--disc)" stroke="var(--green-light)" stroke-width="8"/>
        <circle cx="450" cy="375" r="20" fill="var(--disc)" stroke="var(--green-light)" stroke-width="6"/>
        <text x="450" y="381" text-anchor="middle" font-family="Rubik,sans-serif" font-weight="700" font-size="16" fill="var(--teal-deep)">3</text>
        <g fill="none" stroke="var(--teal-deep)" stroke-width="2">
          <path d="M284 361l4 4 7-8"/>
          <circle cx="280" cy="374" r="4"/><circle cx="290" cy="371" r="4"/><circle cx="300" cy="374" r="4"/>
          <path d="M273 388q7-9 14 0M283 386q7-10 14 0M293 388q7-9 14 0"/>
        </g>
      </g>

      <!-- step 4 -->
      <g transform="translate(0,-30)">
        <line x1="120" y1="475" x2="365" y2="475" stroke="var(--green)" stroke-width="7"/>
        <circle cx="365" cy="475" r="13" fill="var(--teal-mid)"/>
        <circle cx="290" cy="475" r="38" fill="var(--disc)" stroke="var(--teal-deep)" stroke-width="8"/>
        <circle cx="120" cy="475" r="20" fill="var(--disc)" stroke="var(--teal-deep)" stroke-width="6"/>
        <text x="120" y="481" text-anchor="middle" font-family="Rubik,sans-serif" font-weight="700" font-size="16" fill="var(--teal-deep)">4</text>
        <g fill="none" stroke="var(--teal-deep)" stroke-width="1.8">
          <rect x="282" y="459" width="12" height="7" rx="1"/>
          <circle cx="277" cy="472" r="3.5"/><circle cx="303" cy="472" r="3.5"/>
          <path d="M271 490v-10h12M309 490v-10h-12M276 481h28M285 481v9M295 481v9"/>
        </g>
      </g>

      <!-- step 5 -->
      <g transform="translate(0,-25)">
        <line x1="220" y1="575" x2="460" y2="575" stroke="var(--green-light)" stroke-width="7"/>
        <circle cx="220" cy="575" r="13" fill="var(--green)"/>
        <circle cx="290" cy="575" r="38" fill="var(--disc)" stroke="var(--green)" stroke-width="8"/>
        <circle cx="460" cy="575" r="20" fill="var(--disc)" stroke="var(--green)" stroke-width="6"/>
        <text x="460" y="581" text-anchor="middle" font-family="Rubik,sans-serif" font-weight="700" font-size="16" fill="var(--teal-deep)">5</text>
        <g fill="none" stroke="var(--teal-deep)" stroke-width="1.5">
          <circle cx="290" cy="572" r="4"/><path d="M283 584q7-8 14 0"/>
          <circle cx="274" cy="559" r="2.5"/><circle cx="306" cy="559" r="2.5"/><circle cx="274" cy="590" r="2.5"/><circle cx="306" cy="590" r="2.5"/>
          <path d="M282 559h16M274 565v18M306 565v18M282 590h16"/>
        </g>
      </g>

      <!-- step 6 -->
      <g transform="translate(0,3)">
        <line x1="130" y1="675" x2="365" y2="675" stroke="var(--green)" stroke-width="7"/>
        <circle cx="365" cy="675" r="13" fill="var(--teal-mid)"/>
        <circle cx="290" cy="675" r="38" fill="var(--disc)" stroke="var(--teal-deep)" stroke-width="8"/>
        <circle cx="130" cy="675" r="20" fill="var(--disc)" stroke="var(--teal-deep)" stroke-width="6"/>
        <text x="130" y="681" text-anchor="middle" font-family="Rubik,sans-serif" font-weight="700" font-size="16" fill="var(--teal-deep)">6</text>
        <path d="M270 668l8-5 10 6 10-6 12 5v10l-8 6-12-6-8 6-12-6z" fill="var(--teal-deep)"/>
      </g>
    </svg>

    <div class="step-text step-text--left" style="top:160px">
      <h3>Kontaktaufnahme</h3>
      <p>Sie nehmen Kontakt zu uns auf und teilen uns Ihren Personalbedarf, sowie spezielle Stellenanforderungen mit.</p>
    </div>
    <div class="step-text step-text--right" style="top:220px">
      <h3>Vertragsmodalitäten</h3>
      <p>Wir setzen uns mit Ihnen zusammen, besprechen die Einzelheiten und klären die Rahmenbedingungen, individuell auf Sie zugeschnitten.</p>
    </div>
    <div class="step-text step-text--left" style="top:360px">
      <h3>Kandidatenvorauswahl</h3>
      <p>Wir lassen Ihnen vorab übersichtliche CV's potenzieller Kandidat:innen zukommen und Sie treffen eine Vorauswahl bzw. teilen uns eventuelle Anpassungswünsche mit.</p>
    </div>
    <div class="step-text step-text--right" style="top:424px">
      <h3>Vorstellungsgespräche</h3>
      <p>Sie führen die Vorstellungsgespräche mit den Kandidat:innen durch. Unsere Expert:innen begleiten Sie dabei als wichtiges Bindeglied, um bei Missverständnissen und Unklarheiten vorzubeugen.</p>
    </div>
    <div class="step-text step-text--left" style="top:570px">
      <h3>Finale Personalauswahl</h3>
      <p>Sie entscheiden sich für Ihre Wunschmitarbeiter:innen – wir stellen Ihnen zusammen mit einer persönlichen Einschätzung zu den jeweiligen Kandidat:innen alle Informationen und Unterlagen in einem übersichtlichen und informativen Bericht zur Verfügung.</p>
    </div>
    <div class="step-text step-text--right" style="top:658px">
      <h3>Arbeitsvertrag</h3>
      <p>Nach Klärung aller wichtigen Modalitäten und Besonderheiten unterschreibt der/die Bewerber:in seinen/ihren Arbeitsvertrag.</p>
    </div>

    <footer class="contact-band">
      <span>+49 000 555 12 340</span>
      <span>hr@kalvoria.com</span>
      <span>www.kalvoria-hr.com</span>
    </footer>
  </section>

  <section class="page page--firstday">
    <h2 class="firstday-heading">Erster Arbeitstag</h2>
    <p class="firstday-copy">Wir begleiten und betreuen unsere Kandidat:innen über den kompletten Auswahlprozess hinweg bis zum Ende ihrer Probezeit. Nicht selten können wir auch nach der erfolgreichen Vermittlung noch wertvolle Klärungs- und Motivationsarbeit leisten. Außerdem übernehmen wir sowohl Abschlussgespräche, als auch die gesamte Korrespondenz mit allen Bewerber:innen, die am Auswahlverfahren beteiligt waren.</p>
    <div class="firstday-photo" role="img" aria-label="Foto einer lächelnden Pflegekraft in blauer Berufskleidung, die mit beiden Händen zur Seite zeigt"></div>
  </section>

</main>
</body>
</html>
```